Quorva - corporate Business Card

We need a good look and innovative business card for a new start up company based in Los Angeles called "Quorva". We are in a payment business, including payment card, app, and ewallet. We are expert in online payment and Card not present (CNP) transaction.
We need an innovative, modern business card.

Our logo font is Aero Matics

Target Market(s)

Startup - Bank - Online Payment - Card Manufacturing

Industry/Entity Type

Startup

Contact Information for Business Card

phone: 555 014 7396 - Address: 4172 Marlowe blvd, Dorrance Falls, OR 97299

Requirements
Must have
• Message: innovative, professional, expert, high tech, trust, online payment expert, security
Nice to have
• no comment
Should not have
• no Comment

```html
<!DOCTYPE html>
<html lang="en">
<head>
<meta charset="utf-8">
<title>Quorva – Business Card</title>
<link rel="stylesheet" href="https://fonts.googleapis.com/css2?family=Exo+2:wght@400;500;600;700&display=swap">
<style>
  :root {
    --backdrop: #6b6b6b;
    --card-black: #0c0c10;
    --card-black-soft: #1a1a1f;
    --brand-red: #b81e2d;
    --paper-white: #f7f7f8;
  }
  * { margin: 0; padding: 0; box-sizing: border-box; }
  html, body {
    width: 1200px; height: 900px; overflow: hidden;
    background: var(--backdrop);
    font-family: "Exo 2", sans-serif;
  }
  .stage { position: relative; width: 1200px; height: 900px; }
  .card {
    position: absolute; top: 271px;
    width: 458px; height: 282px;
    border-radius: 14px; overflow: hidden;
  }
  .card--front { left: 137px; background: var(--brand-red); }
  .card--back {
    left: 626px;
    background: linear-gradient(180deg, var(--card-black) 0%, var(--card-black-soft) 100%);
  }
  .front__band {
    position: absolute; left: 0; top: 0; width: 113px; height: 100%;
    background: linear-gradient(180deg, var(--card-black) 0%, var(--card-black-soft) 100%);
  }
  .front__badge {
    position: absolute; left: 59px; top: 67px;
    width: 146px; height: 146px; border-radius: 50%;
    background: var(--paper-white);
    display: flex; align-items: center; justify-content: center;
    color: var(--brand-red); font-weight: 700; font-size: 30px;
  }
  .front__identity, .front__contact, .front__address {
    position: absolute; right: 27px; text-align: right; color: var(--paper-white);
  }
  .front__identity { top: 24px; }
  .front__name { font-size: 27px; font-weight: 700; line-height: 32px; }
  .front__role { font-size: 16px; font-weight: 600; line-height: 24px; }
  .front__contact { top: 99px; }
  .contact-line {
    display: flex; align-items: center; justify-content: flex-end; gap: 8px;
    font-size: 16px; font-weight: 500; height: 23px;
  }
  .contact-line svg { width: 20px; height: 20px; }
  .front__address { bottom: 29px; font-size: 14px; font-weight: 500; }
  .back__mark {
    position: absolute; left: 98px; top: 101px;
    display: flex; align-items: center; gap: 10px;
  }
  .back__dot { width: 78px; height: 78px; border-radius: 50%; background: var(--brand-red); }
  .back__name { color: var(--brand-red); font-size: 48px; font-weight: 600; line-height: 1; }
</style>
</head>
<body>
<main class="stage">
  <section class="card card--front">
    <div class="front__band"></div>
    <div class="front__badge">Quorva</div>
    <div class="front__identity">
      <p class="front__name">Dana Whitfield</p>
      <p class="front__role">Director</p>
    </div>
    <div class="front__contact">
      <p class="contact-line">555 014 7396
        <svg viewBox="0 0 20 20" aria-hidden="true"><circle cx="10" cy="10" r="10" fill="#f7f7f8"/><rect x="6.5" y="4" width="7" height="12" rx="1.5" fill="#b81e2d"/><rect x="7.8" y="5.6" width="4.4" height="7.4" fill="#f7f7f8"/></svg>
      </p>
      <p class="contact-line">www.quorva.com
        <svg viewBox="0 0 20 20" aria-hidden="true"><circle cx="10" cy="10" r="10" fill="#f7f7f8"/><circle cx="10" cy="10" r="5.5" fill="none" stroke="#b81e2d" stroke-width="1.5"/><path d="M4.5 10h11M10 4.5c-2.5 3-2.5 8 0 11M10 4.5c2.5 3 2.5 8 0 11" fill="none" stroke="#b81e2d" stroke-width="1.2"/></svg>
      </p>
    </div>
    <p class="front__address">4172 Marlowe blvd, Dorrance Falls, OR 97299</p>
  </section>
  <section class="card card--back">
    <div class="back__mark">
      <span class="back__dot"></span>
      <span class="back__name">Quorva</span>
    </div>
  </section>
</main>
</body>
</html>
```